ZESTORAMA Business Card Design

ZESTORAMA
Zestorama is a food van, serving high vibe delicious food to go. This business is dedicated to healthy delicious feel good food, beauty in service and a sustainable planet.

The van will operate in the south west of western Australia at music festivals events markets wherever people need great food to go!

I like the idea of vibrant green mixed with a yellow?? background with some rays like the sun through the background.
The font needs to say vibrant energetic
TO ME -vibrant energetic font has to appear to be on the move - perhaps with shading??

I like fusha if that works for font? but the colour has to say food too.

I would like a symbol on the card a simple V turned into a womans raised arms. This should be vibrant too.
Thank you
Blessings
Marisol

Target Market(s)

target lovers of healthy high vibe food. music festival goers. age 18- 50 feel. audiance conscious eaters of feel great food

Industry/Entity Type

Events

Contact Information for Business Card

ZESTORAMA
High Vibe Food
Van
Marisol -owner/opperator
0471583906
Face book symbol - ZESTORAMA

on the I would like a logo of a simple V turned into a womans arms up toward the sky flip side

My number and name again
Zestorama- feel great mobile food
Festivals, events, markets & where high vibe food 2 go is appreciated

Requirements
Nice to have
• Moving energetic font
colour that says high vibe and healthy food

a logo that is a simple V turned into a woman's raised arms in gratitude

```html
<!DOCTYPE html>
<html lang="en">
<head>
<meta charset="utf-8">
<title>Zestorama Business Card</title>
<link href="https://fonts.googleapis.com/css2?family=Exo+2:wght@400;500;700;800&display=swap" rel="stylesheet">
<style>
  :root {
    --backdrop: #2b2b2b;
    --card-dark: #1f1f1f;
    --green-deep: #1fae4b;
    --green-mid: #5cbf3a;
    --green-glow: #b9cf32;
    --white: #ffffff;
    --icon-dark: #1c1c1c;
    --brand-green: #2f9a3a;
    --tagline: #b9cf32;
  }
  * { margin: 0; padding: 0; box-sizing: border-box; }
  html, body { width: 1200px; height: 821px; overflow: hidden; }
  body {
    background: var(--backdrop);
    font-family: "Exo 2", sans-serif;
    position: relative;
  }
  .card {
    position: absolute;
    width: 540px;
    height: 320px;
    background: var(--card-dark);
    overflow: hidden;
  }
  .card--front { left: 40px; top: 250px; }
  .card--back { left: 620px; top: 250px; }

  .contact-panel {
    position: absolute;
    left: 210px; top: 0;
    width: 330px; height: 215px;
    background: radial-gradient(circle at 60% 45%, var(--green-glow) 0%, var(--green-mid) 40%, var(--green-deep) 100%);
    border-bottom: 4px solid #151515;
  }
  .name {
    position: absolute;
    top: 22px;
    color: var(--white);
    font-size: 27px;
    font-weight: 500;
    letter-spacing: 2px;
  }
  .name--first { left: 48px; }
  .name--last { left: 222px; }
  .role {
    position: absolute;
    left: 222px; top: 56px;
    color: var(--white);
    font-size: 12px;
    letter-spacing: 1px;
  }
  .contact-list { list-style: none; }
  .contact-item {
    position: absolute;
    left: 210px;
    height: 26px;
    display: flex;
    align-items: center;
  }
  .contact-item__tab {
    width: 28px; height: 26px;
    margin-left: -28px;
    background: var(--green-mid);
    display: flex;
    align-items: center;
    justify-content: center;
  }
  .contact-item__text {
    margin-left: 14px;
    color: var(--white);
    font-size: 13px;
    letter-spacing: 0.5px;
  }
  .contact-item:nth-child(1) { top: 92px; }
  .contact-item:nth-child(2) { top: 122px; }
  .contact-item:nth-child(3) { top: 152px; }
  .contact-item:nth-child(4) { top: 182px; }

  .brand {
    position: absolute;
    left: 48px; bottom: 52px;
    display: flex;
    align-items: center;
    gap: 12px;
  }
  .brand__mark {
    width: 30px; height: 30px;
    border-radius: 50%;
    background: var(--brand-green);
  }
  .brand__name {
    color: var(--brand-green);
    font-size: 44px;
    font-weight: 800;
    line-height: 1;
  }
  .tagline {
    position: absolute;
    left: 90px; bottom: 28px;
    color: var(--tagline);
    font-size: 13px;
    font-weight: 500;
    letter-spacing: 3px;
  }

  .back-frame {
    position: absolute;
    inset: 34px;
    border: 12px solid var(--white);
  }
</style>
</head>
<body>
  <section class="card card--front" aria-label="Business card front">
    <div class="contact-panel"></div>
    <h1 class="name name--first">DORIAN</h1>
    <h1 class="name name--last">KELLER</h1>
    <p class="role">OWNER / OPERATOR</p>
    <ul class="contact-list">
      <li class="contact-item">
        <span class="contact-item__tab">
          <svg width="12" height="14" viewBox="0 0 12 14"><path d="M6 0a5 5 0 0 1 5 5c0 4-5 9-5 9S1 9 1 5a5 5 0 0 1 5-5z" fill="var(--icon-dark)"/><circle cx="6" cy="5" r="2" fill="var(--green-mid)"/></svg>
        </span>
        <span class="contact-item__text">041 12th floor Harbour Lane Road BNT</span>
      </li>
      <li class="contact-item">
        <span class="contact-item__tab">
          <svg width="13" height="13" viewBox="0 0 13 13"><path d="M2 1l3 0 1 3-2 1.5a7 7 0 0 0 3.5 3.5L9 7l3 1v3l-1.5 1.5C5 12 1 8 0.5 2.5z" fill="var(--icon-dark)"/></svg>
        </span>
        <span class="contact-item__text">013 482 5071</span>
      </li>
      <li class="contact-item">
        <span class="contact-item__tab">
          <svg width="14" height="10" viewBox="0 0 14 10"><rect x="0.5" y="0.5" width="13" height="9" fill="var(--icon-dark)"/><path d="M0.5 0.5L7 6l6.5-5.5" stroke="var(--green-mid)" fill="none"/></svg>
        </span>
        <span class="contact-item__text">hello@zestmail.com</span>
      </li>
      <li class="contact-item">
        <span class="contact-item__tab">
          <svg width="14" height="14" viewBox="0 0 14 14"><circle cx="7" cy="7" r="6" fill="var(--icon-dark)"/><g stroke="var(--green-mid)" fill="none" stroke-width="0.9"><ellipse cx="7" cy="7" rx="2.5" ry="6"/><path d="M1 7h12M2 4h10M2 10h10"/></g></svg>
        </span>
        <span class="contact-item__text">www.zestoramafood.com</span>
      </li>
    </ul>
    <div class="brand">
      <span class="brand__mark" aria-hidden="true"></span>
      <p class="brand__name">Zestorama</p>
    </div>
    <p class="tagline">HIGH VIBE FOOD VAN</p>
  </section>

  <section class="card card--back" aria-label="Business card back">
    <div class="back-frame"></div>
  </section>
</body>
</html>
```